Lumavento business card

We need a modern business card - With our 4 colors - See web: www.lumavento.dk

I have attached logo and som old business Cards we have - Lets Make the new ones shine...:-) -

Industry/Entity Type

Business

Requirements
Must have
• the logo with lumavento only,

```html
<!DOCTYPE html>
<html lang="da">
<head>
<meta charset="utf-8">
<title>Lumavento business card</title>
<link rel="stylesheet" href="https://fonts.googleapis.com/css2?family=Josefin+Sans:wght@300;400&display=swap">
<style>
  :root {
    --bg: #ece9e4;
    --card-dark: #333333;
    --lime: #8cc63f;
    --pink: #c2368f;
    --orange: #e8822e;
    --purple: #6b2f86;
    --yellow: #c9c23a;
  }
  * { margin: 0; padding: 0; box-sizing: border-box; }
  html, body { width: 1200px; height: 1023px; overflow: hidden; }
  body {
    background: var(--bg);
    font-family: "Josefin Sans", sans-serif;
    position: relative;
  }
  .card {
    position: absolute;
    left: 320px;
    width: 560px;
    height: 340px;
    border-radius: 6px;
    box-shadow: 0 6px 18px rgba(0,0,0,.18);
    overflow: hidden;
  }
  .card--front { top: 140px; background: var(--card-dark); }
  .card--back {
    top: 543px;
    background: linear-gradient(160deg, var(--yellow) 0%, var(--orange) 28%, #e86a6a 42%, var(--pink) 66%, var(--purple) 100%);
  }

  /* identity block */
  .identity { position: absolute; left: 44px; top: 78px; width: 230px; }
  .brand { display: flex; align-items: center; gap: 12px; }
  .brand__dot { width: 18px; height: 18px; border-radius: 50%; background: var(--lime); }
  .brand__name {
    font-weight: 300; font-size: 32px; letter-spacing: 2px; color: var(--orange);
  }
  .identity__rule { height: 2px; background: var(--lime); margin: 14px 0 16px; width: 220px; }
  .person__name { font-weight: 300; font-size: 27px; letter-spacing: 1px; color: var(--lime); }
  .person__title { font-weight: 400; font-size: 20px; letter-spacing: 1px; color: var(--pink); margin-top: 10px; }

  /* contact rail */
  .rail { position: absolute; left: 318px; top: 0; width: 4px; height: 340px; }
  .rail__seg { position: absolute; left: 0; width: 4px; }
  .rail__seg--pink { top: 0; height: 130px; background: var(--pink); }
  .rail__seg--lime { top: 130px; height: 80px; background: var(--lime); }
  .rail__seg--orange { top: 210px; height: 90px; background: var(--orange); }
  .rail__seg--purple { top: 300px; height: 40px; background: var(--purple); }

  .contact { position: absolute; left: 302px; display: flex; align-items: center; gap: 14px; }
  .contact__icon {
    width: 36px; height: 36px; border-radius: 50%;
    display: flex; align-items: center; justify-content: center; flex: none;
  }
  .contact__icon--pink { background: var(--pink); }
  .contact__icon--lime { background: var(--lime); }
  .contact__icon--orange { background: var(--orange); }
  .contact__text { color: var(--lime); font-size: 16px; line-height: 24px; letter-spacing: 1.5px; font-weight: 300; }
  .contact--address { top: 52px; }
  .contact--phone { top: 146px; }
  .contact--mail { top: 240px; }
</style>
</head>
<body>
  <section class="card card--front" aria-label="Visitkort forside">
    <div class="identity">
      <div class="brand">
        <span class="brand__dot"></span>
        <span class="brand__name">lumavento</span>
      </div>
      <div class="identity__rule"></div>
      <p class="person__name">Jonas Halvorsen</p>
      <p class="person__title">Salgsdirektør</p>
    </div>

    <div class="rail">
      <span class="rail__seg rail__seg--pink"></span>
      <span class="rail__seg rail__seg--lime"></span>
      <span class="rail__seg rail__seg--orange"></span>
      <span class="rail__seg rail__seg--purple"></span>
    </div>

    <div class="contact contact--address">
      <span class="contact__icon contact__icon--pink">
        <svg width="18" height="18" viewBox="0 0 18 18"><path d="M2 8 L16 2 L10 16 L8.5 9.5 Z" fill="#3a3a3a"/></svg>
      </span>
      <p class="contact__text">Lindevej 14<br>2100 København Ø</p>
    </div>

    <div class="contact contact--phone">
      <span class="contact__icon contact__icon--lime">
        <svg width="20" height="18" viewBox="0 0 20 18"><path d="M2 6 Q10 0 18 6 L16 8 L13 7 L13 5 Q10 4 7 5 L7 7 L4 8 Z" fill="#3a3a3a"/><rect x="4" y="9" width="12" height="7" rx="1.5" fill="#3a3a3a"/><circle cx="10" cy="12.5" r="2" fill="#8cc63f"/></svg>
      </span>
      <p class="contact__text">+45 31 42 67 80<br>+45 52 19 73 46</p>
    </div>

    <div class="contact contact--mail">
      <span class="contact__icon contact__icon--orange">
        <svg width="20" height="16" viewBox="0 0 20 16"><rect x="1" y="2" width="18" height="12" rx="1" fill="#3a3a3a"/><path d="M1.5 2.5 L10 9 L18.5 2.5" stroke="#e8822e" stroke-width="1.4" fill="none"/></svg>
      </span>
      <p class="contact__text">jh@lumavento.dk<br>info@lumavento.dk</p>
    </div>
  </section>

  <section class="card card--back" aria-label="Visitkort bagside"></section>
</body>
</html>
```